Electrician Letterhead Design MVR

We need some letterhead for our bills and other papers.
Customer address is on the right side (Swiss format)
A4 format

Design should also be applicable on Cards

Target Market(s)

Private Customers, Small Business

Industry/Entity Type

Electrician

Other font styles liked:
• incised 901

Colors
00AB8E
00BBA5
67D7C9
C6EFE9
E9F9F6

```html
<!DOCTYPE html>
<html lang="en">
<head>
<meta charset="utf-8">
<title>MVR Letterhead</title>
<link href="https://fonts.googleapis.com/css2?family=Lato:wght@400;700;900&family=Great+Vibes&display=swap" rel="stylesheet">
<style>
  :root {
    --teal-deep: #049c8a;
    --teal-light: #6fbfb6;
    --ink: #2b2b2b;
    --ink-soft: #444444;
    --paper: #ffffff;
    --backdrop: #e4e4e6;
  }
  * { box-sizing: border-box; margin: 0; padding: 0; }
  html, body {
    width: 1200px; height: 874px; overflow: hidden;
    background: var(--backdrop);
    font-family: "Lato", Arial, sans-serif;
    color: var(--ink);
  }
  .letterhead {
    position: absolute; left: 306px; top: 22px;
    width: 587px; height: 830px;
    background: var(--paper);
    overflow: hidden;
    box-shadow: 0 2px 10px rgba(0,0,0,.12);
  }
  .brand { position: absolute; left: 56px; top: 92px; display: flex; flex-direction: column; }
  .brand-name {
    font-weight: 900; font-size: 50px; line-height: 1; letter-spacing: 1px;
    color: var(--teal-deep); display: flex; align-items: center; gap: 8px;
  }
  .brand-mark { width: 12px; height: 12px; background: var(--teal-deep); }
  .brand-sub { font-weight: 700; font-size: 8.5px; letter-spacing: .4px; margin-top: 4px; color: var(--ink); }
  .contact {
    position: absolute; left: 388px; top: 40px;
    font-size: 7.5px; line-height: 1.45; color: var(--ink); font-style: normal;
  }
  .contact-row { display: flex; align-items: center; gap: 4px; margin-left: 10px; }
  .contact-row svg { width: 7px; height: 7px; fill: var(--teal-deep); }
  .letter { position: absolute; left: 72px; top: 198px; width: 460px; font-size: 9.6px; line-height: 1.35; color: var(--ink-soft); }
  .date { font-size: 10.5px; margin-bottom: 12px; }
  .recipient { font-size: 10.5px; line-height: 1.3; margin-bottom: 12px; }
  .recipient p + p { margin-top: 12px; }
  .salutation { font-weight: 700; font-size: 12px; color: var(--ink); margin-bottom: 12px; }
  .body p { margin-bottom: 18px; }
  .closing { margin-top: 18px; font-size: 10px; }
  .signature { font-family: "Great Vibes", cursive; font-size: 36px; color: var(--ink); margin: 6px 0 0 30px; }
  .footer-band {
    position: absolute; left: 0; bottom: 0;
    width: 587px; height: 110px;
    background: linear-gradient(90deg, var(--teal-light) 0%, var(--teal-deep) 70%);
  }
</style>
</head>
<body>
  <main class="letterhead">
    <header>
      <div class="brand">
        <div class="brand-name">MVR<span class="brand-mark"></span></div>
        <div class="brand-sub">Elektrotechnik Vogel GmbH</div>
      </div>
      <address class="contact">
        <div>42 Lindenweg 7,</div>
        <div>Brookfield, NY 11420</div>
        <div class="contact-row"><svg viewBox="0 0 10 10"><path d="M2 0.5 L4 0.5 L4.8 3 L3.6 4 C4.2 5.3 4.8 5.9 6 6.4 L7 5.2 L9.5 6 L9.5 8 C9.5 9 8.8 9.5 8 9.5 C4 9.2 0.8 6 0.5 2 C0.5 1.2 1 0.5 2 0.5Z"/></svg>704-555-0182</div>
        <div class="contact-row"><svg viewBox="0 0 10 10"><path d="M0 2 H10 V8.5 H0Z M0.6 2.4 L5 5.8 L9.4 2.4 L9.4 2.6 L5 6.2 L0.6 2.6Z" fill-rule="evenodd"/></svg>hello@mvrmail.com</div>
        <div class="contact-row"><svg viewBox="0 0 10 10"><circle cx="5" cy="5" r="4.5"/></svg>www.mvr-elektro.com</div>
      </address>
    </header>

    <section class="letter">
      <div class="date">Feb-03-2022</div>
      <div class="recipient">
        <p>Mr. Peter Hale<br>President</p>
        <p>Northgate Corporation<br>123 Street Name, Suite# 10<br>City, State, 120023</p>
      </div>
      <div class="salutation">Dear Mr, Peter</div>
      <div class="body">
        <p>Lorem ipsum dolor sit amet, consectetur adipisicing elit, sed do eiusmod tempor incididunt ut labore et dolore magna aliqua. Ut enim ad minim veniam, quis nostrud exercitation ullamco laboris nisi ut aliquip ex ea commodo consequat. Duis aute irure dolor in reprehenderit in voluptate velit esse cillum dolore eu fugiat nulla pariatur.</p>
        <p>Lorem ipsum dolor sit amet, consectetur adipisicing elit, sed do eiusmod tempor incididunt ut labore et dolore magna aliqua. Ut enim ad minim veniam, quis nostrud exercitation ullamco laboris nisi ut aliquip ex ea commodo consequat. Duis aute irure dolor in reprehenderit in voluptate velit esse cillum dolore eu fugiat nulla pariatur.</p>
        <p>Lorem ipsum dolor sit amet, consectetur adipisicing elit, sed do eiusmod tempor incididunt ut labore et dolore magna aliqua. Ut enim ad minim veniam, quis nostrud exercitation ullamco laboris nisi ut aliquip ex ea commodo consequat.</p>
        <p>Excepteur sint occaecat cupidatat non proident, sunt in culpa qui officia deserunt mollit anim id est laborum. re et dolore magnam aliquam quaerat voluptatem.</p>
      </div>
      <div class="closing">Regards</div>
      <div class="signature">Daniel Berger</div>
    </section>

    <div class="footer-band" role="img" aria-label="Teal decorative footer area"></div>
  </main>
</body>
</html>
```